Business Card Design

Hi I need a business card designed, we already have the business name logo artwork and would like some concept ideas for the Bus Card layout.
On the back of the card i want to include the products and services that we offer.
We are a Plastics Sheeting manufacture based in Perth Australia.

                                       

We need a BC design for a company called Tarvo Plastics based in Perth Australia.

We supply from DIY to Trade & Industrial  Engineering Markets.

We specialise in:

·         Cut to size panels  (all shapes and sizes)

·         Plastics fabrication & Welding

·         Custom Designs

·         Plastic Repairs

·         PVC Pipe Slotting & PVC Pipe Threading

·         Supplier of all types of engineering plastics and profiles.

Including:           Acrylic / Clarvene

                               Polycarbonate / Dorvil

                               Prismatic Light Diffuser

                               Vantrib

                               HDPE / UHMWPE

                               PVC / PVC Foam

                               Nylon

                               HIPS

```html
<!DOCTYPE html>
<html lang="en">
<head>
<meta charset="utf-8">
<title>Tarvo Plastics – Business Card</title>
<link href="https://fonts.googleapis.com/css2?family=Open+Sans:wght@400;600;700;800&display=swap" rel="stylesheet">
<style>
  :root {
    --navy: #1d2c5e;
    --navy-deep: #17244f;
    --orange: #e8871e;
    --gold: #f0a81c;
    --ink: #555a66;
    --paper: #ffffff;
    --backdrop: #e9e9ec;
    --rule: #b9bcc6;
  }
  * { box-sizing: border-box; margin: 0; padding: 0; }
  html, body {
    width: 1200px; height: 720px; overflow: hidden;
    background: var(--backdrop);
    font-family: "Open Sans", sans-serif;
  }
  .canvas { position: relative; width: 1200px; height: 720px; }
  .card {
    position: absolute; top: 195px;
    width: 540px; height: 330px;
    overflow: hidden;
    box-shadow: 0 6px 18px rgba(0,0,0,.18);
  }

  /* ---------- Front ---------- */
  .card--front { left: 40px; background: var(--paper); }
  .front-waves { position: absolute; inset: 0; }
  .brand {
    position: absolute; display: flex; align-items: center; gap: 10px;
    font-weight: 800; letter-spacing: -0.5px; white-space: nowrap;
  }
  .brand__mark { width: 18px; height: 18px; }
  .card--front .brand {
    top: 28px; left: 0; right: 0; justify-content: center;
    font-size: 42px; color: var(--navy);
  }
  .card--front .brand__mark { background: var(--orange); }

  .person {
    position: absolute; top: 100px; right: 290px; text-align: right;
    color: var(--ink); font-size: 12.5px; line-height: 1.45;
  }
  .person__name { color: var(--navy); font-weight: 700; font-size: 17px; line-height: 1.2; }
  .person__title { color: var(--orange); font-size: 12px; margin-bottom: 10px; }

  .divider-v {
    position: absolute; left: 268px; top: 102px; width: 1px; height: 86px;
    background: var(--rule);
  }
  .contacts {
    position: absolute; top: 100px; left: 282px; list-style: none;
    color: var(--ink); font-size: 12.5px;
  }
  .contacts li { display: flex; align-items: center; gap: 8px; height: 22px; white-space: nowrap; }
  .contacts svg { width: 13px; height: 13px; flex: none; }

  .legal {
    position: absolute; bottom: 16px; left: 0; right: 0; text-align: center;
    color: var(--paper); font-size: 12.5px; letter-spacing: .2px;
  }

  /* ---------- Back ---------- */
  .card--back { left: 620px; background: var(--navy); color: var(--paper); }
  .card--back .brand {
    top: 22px; left: 0; right: 0; justify-content: center;
    font-size: 46px; color: var(--paper);
  }
  .card--back .brand__mark { background: var(--paper); }
  .tagline {
    position: absolute; top: 96px; left: 0; right: 0; text-align: center;
    font-weight: 700; font-size: 13.5px; line-height: 1.35;
  }
  .offer { position: absolute; top: 148px; font-size: 12.5px; line-height: 1.32; }
  .offer--services { left: 22px; width: 300px; }
  .offer--materials { left: 350px; width: 180px; }
  .offer__heading { color: var(--gold); font-weight: 700; font-size: 16px; margin-bottom: 4px; }
  .offer__list { list-style: none; }
  .offer__list li { position: relative; padding-left: 12px; }
  .offer__list li::before {
    content: ""; position: absolute; left: 0; top: 6px;
    width: 5px; height: 5px; border-radius: 50%; background: var(--gold);
  }
  .offer__pair { display: flex; gap: 10px; }
  .offer__pair span { position: relative; }
  .offer__pair span + span { padding-left: 12px; }
  .offer__pair span + span::before {
    content: ""; position: absolute; left: 0; top: 6px;
    width: 5px; height: 5px; border-radius: 50%; background: var(--gold);
  }
  .divider-back {
    position: absolute; left: 332px; top: 150px; width: 1px; height: 140px;
    background: rgba(255,255,255,.45);
  }
</style>
</head>
<body>
<main class="canvas">

  <section class="card card--front" aria-label="Card front">
    <svg class="front-waves" viewBox="0 0 540 330" preserveAspectRatio="none" aria-hidden="true">
      <path d="M0 276 C160 312 380 276 540 214 L540 330 L0 330 Z" fill="var(--navy)"/>
      <path d="M0 262 C160 300 380 262 540 200" fill="none" stroke="var(--orange)" stroke-width="6"/>
      <path d="M0 254 C160 292 380 254 540 192" fill="none" stroke="var(--rule)" stroke-width="1"/>
    </svg>

    <div class="brand"><span class="brand__mark"></span>Tarvo Plastics</div>

    <div class="person">
      <div class="person__name">Your Name</div>
      <div class="person__title">Title</div>
      <div>Unit 4/18 Harlow Crescent</div>
      <div>Brennock Vale WA 6150</div>
      <div>PO Box 2270</div>
      <div>Brennock Vale DC WA 6971</div>
    </div>

    <div class="divider-v"></div>

    <ul class="contacts">
      <li>
        <svg viewBox="0 0 16 16" aria-hidden="true"><circle cx="8" cy="8" r="8" fill="var(--orange)"/><path d="M5 4.5c.6-.4 1.2 0 1.5.6l.5 1.2c.1.4-.1.7-.4.9 .4 1 1.1 1.7 2.1 2.1.2-.3.5-.5.9-.4l1.2.5c.6.3 1 .9.6 1.5-.5.7-1.4 1-2.3.6C7 10.6 5.4 9 4.5 7.1 4.1 6.2 4.3 5.2 5 4.5z" fill="#fff"/></svg>
        08 9400 1350
      </li>
      <li>
        <svg viewBox="0 0 16 16" aria-hidden="true"><rect x="4" y="1" width="8" height="14" rx="1.5" fill="var(--orange)"/><rect x="5.5" y="3" width="5" height="8" fill="#fff"/><circle cx="8" cy="13" r=".8" fill="#fff"/></svg>
        123-456-7890
      </li>
      <li>
        <svg viewBox="0 0 16 16" aria-hidden="true"><rect x="4" y="2" width="8" height="5" fill="var(--orange)"/><rect x="1" y="6" width="14" height="6" rx="1.5" fill="var(--orange)"/><rect x="4" y="10" width="8" height="4" fill="#fff" stroke="var(--orange)"/></svg>
        08 9400 1360
      </li>
      <li>
        <svg viewBox="0 0 16 16" aria-hidden="true"><rect x="1" y="3" width="14" height="10" rx="1.5" fill="var(--orange)"/><path d="M1.5 4l6.5 5 6.5-5" fill="none" stroke="#fff" stroke-width="1.3"/></svg>
        sales@tarvoplastics.com.au
      </li>
    </ul>

    <p class="legal">Halden Group Pty Ltd T/A Tarvo Plastics ABN: TBA</p>
  </section>

  <section class="card card--back" aria-label="Card back">
    <div class="brand"><span class="brand__mark"></span>Tarvo Plastics</div>

    <p class="tagline">The Products And Services That We Offer<br>Are Supplied From Diy To Trade &amp; Industrial Engineering Markets</p>

    <div class="offer offer--services">
      <h2 class="offer__heading">We specialise in:</h2>
      <ul class="offer__list">
        <li>Cut to size panels (all shapes and sizes)</li>
        <li>Plastics fabrication &amp; Welding</li>
        <li>Custom Designs</li>
        <li>Plastic Repairs</li>
        <li>PVC Pipe Slotting &amp; PVC Pipe Threading</li>
        <li>Supplier of all types of engineering plastics and profiles</li>
      </ul>
    </div>

    <div class="divider-back"></div>

    <div class="offer offer--materials">
      <h2 class="offer__heading">Including:</h2>
      <ul class="offer__list">
        <li>Acrylic / Clarvene</li>
        <li>Polycarbonate / Dorvil</li>
        <li>Prismatic Light Diffuser</li>
        <li class="offer__pair"><span>Vantrib</span><span>HDPE / UHMWPE</span></li>
        <li>PVC / PVC Foam</li>
        <li class="offer__pair"><span>Nylon</span><span>HIPS</span></li>
      </ul>
    </div>
  </section>

</main>
</body>
</html>
```